Graphic Design for a block-note A4 size

We need a graphic design for a simple block-note A4 size. The product consists of 50 sheets in VERTICAL A4 (21x29,7cm) size, simply glued on top, without cover. We would like to have proposals with double application: one for home users without a logo and one for professionals with an area "put your logo here".
The graphics should be simple and attractive, elegant and pleasant to keep on your desk.
The block-notes may have standard squares (5 or 10 mm) or stripes (10 mm spaced) on the background to make the writing easy.
Feel free to use your creativity, the only limit is the CMYK color space.

We will upload some block-note simple templates and 3D sample images to help you.

Reason: We want to give you more few days to work on your graphic designs.

• The graphics should be simple and attractive, elegant and pleasant to keep on your desk.

• The block-notes may have standard squares (5 or 10 mm) or stripes (10 mm spaced) on the background to make the writing easy.

```html
<!DOCTYPE html>
<html lang="en">
<head>
<meta charset="UTF-8">
<title>A4 Block-Note – Home and Professional Editions</title>
<link rel="stylesheet" href="https://fonts.googleapis.com/css2?family=Archivo:wght@800&display=swap">
<style>
  :root {
    --canvas-bg: #ffffff;
    --paper: #ffffff;
    --paper-edge: #d9d9d9;
    --frame-orange: #f39a1e;
    --grid-line: #e3e6ea;
    --wave-yellow: #fbe889;
    --wave-orange: #f4a53a;
    --logo-orange: #f28c12;
  }
  * { box-sizing: border-box; margin: 0; padding: 0; }
  html, body {
    width: 1200px;
    height: 900px;
    overflow: hidden;
    background: var(--canvas-bg);
  }
  .stage {
    position: relative;
    width: 1200px;
    height: 900px;
  }
  .note-sheet {
    position: absolute;
    top: 110px;
    width: 480px;
    height: 679px;
    background: var(--paper);
    border: 1px solid var(--paper-edge);
    overflow: hidden;
  }
  .note-sheet--home { left: 90px; }
  .note-sheet--pro { left: 630px; }

  .writing-grid {
    position: absolute;
    left: 32px;
    right: 32px;
    top: 52px;
    bottom: 42px;
    border: 1px solid var(--frame-orange);
    background-image:
      linear-gradient(to right, var(--grid-line) 1px, transparent 1px),
      linear-gradient(to bottom, var(--grid-line) 1px, transparent 1px);
    background-size: 16px 16px;
    background-position: -1px -1px;
  }

  .wave-ornament {
    position: absolute;
    left: 0;
    right: 0;
    bottom: 0;
    height: 210px;
    background:
      radial-gradient(ellipse 40% 55% at 62% 45%, rgba(244,165,58,0.55), transparent 70%),
      radial-gradient(ellipse 30% 45% at 18% 55%, rgba(244,165,58,0.4), transparent 70%),
      linear-gradient(to top, rgba(251,232,137,0.75), rgba(251,232,137,0.35) 55%, rgba(251,232,137,0) 100%);
  }

  .logo-placeholder {
    position: absolute;
    top: 34px;
    left: 220px;
    width: 132px;
    height: 132px;
    border: 1px solid var(--frame-orange);
    border-radius: 50%;
    background: var(--paper);
    display: flex;
    align-items: center;
    justify-content: center;
  }
  .logo-placeholder__text {
    font-family: "Archivo", Arial, sans-serif;
    font-weight: 800;
    font-size: 28px;
    letter-spacing: 0.5px;
    color: var(--logo-orange);
  }
</style>
</head>
<body>
  <main class="stage">
    <section class="note-sheet note-sheet--home" aria-label="Block-note sheet, home edition">
      <div class="writing-grid"></div>
      <div class="wave-ornament" role="img" aria-label="Flowing yellow and orange line waves with small dots along the bottom of the sheet"></div>
    </section>

    <section class="note-sheet note-sheet--pro" aria-label="Block-note sheet, professional edition">
      <div class="writing-grid"></div>
      <div class="logo-placeholder"><span class="logo-placeholder__text">LOGO</span></div>
      <div class="wave-ornament" role="img" aria-label="Flowing yellow and orange line waves with small dots along the bottom of the sheet"></div>
    </section>
  </main>
</body>
</html>
```